Website for data analytics startup

I have a landing page up at http://quenvo.io I need to expand this into a basic company website. I want something similar to this design: http://kelmarix.com/examples/carousel/

I need HTML and CSS for each of the designs, once they are approved. I need the following pages: home page, product, team, blog, and a design for the container of our demo application.

Our logo is attached and also available here: https://files.dravistore.net/quenvo.public/LOGO-colour.png I would like the website branding to match the logo.

I need a blog design with CSS that works with Tumblr.

Our app can be seen at http://demo.quenvo.io Please don't change the look of the network graph itself, only the surrounding content.

For CSS, I want you to use Bootstrap or Foundation as the starting point.

Target Market(s)

Sales and marketing, strategy

Industry/Entity Type

It Company

Coding

Coded - Design and coding required

Number of Pages Required

4 page

Font styles to use
Serif
Sans Serif

Requirements
Must have
• Clean, healthy appeal. Must work well with our logo. Blog page must integrate with Tumblr easily. Must use Bootstrap or Foundation for the starting point of the HTML/CSS.
Should not have
• Ugly crap, flash looking design. NO FLASH.

```html
<!DOCTYPE html>
<html lang="en">
<head>
<meta charset="utf-8">
<title>Quenvo — Maps Markets to Drive Sales and Marketing</title>
<link href="https://fonts.googleapis.com/css2?family=Raleway:wght@400;500;600&family=Open+Sans:wght@400;600&display=swap" rel="stylesheet">
<style>
  :root {
    --navy-deep: #06123a;
    --navy-mid: #123a82;
    --ink: #1e2a30;
    --ink-soft: #555d63;
    --muted: #8a9096;
    --brand-teal: #14475f;
    --brand-green: #6cbb3c;
    --sky: #5ab4e6;
    --sky-light: #8fd0f2;
    --field: #b5e4fa;
    --field-text: #3f7a98;
    --footer: #062b42;
    --white: #ffffff;
  }
  * { box-sizing: border-box; margin: 0; padding: 0; }
  html, body { width: 851px; height: 1200px; overflow: hidden; background: var(--white); }
  body { position: relative; font-family: "Raleway", sans-serif; color: var(--ink); }

  /* Header */
  .site-header { position: absolute; left: 0; top: 0; width: 851px; height: 73px; background: var(--white); }
  .brand { position: absolute; left: 146px; top: 24px; display: flex; align-items: center; gap: 6px; }
  .brand-dot { width: 12px; height: 12px; border-radius: 50%; background: var(--brand-green); }
  .brand-name { font-family: "Raleway", sans-serif; font-weight: 600; font-size: 26px; color: var(--brand-teal); letter-spacing: -0.3px; }
  .main-nav { position: absolute; top: 32px; left: 337px; display: flex; gap: 0; }
  .main-nav a { font-size: 10.5px; color: #4a4f55; text-decoration: none; position: absolute; white-space: nowrap; }

  /* Hero */
  .hero { position: absolute; left: 0; top: 73px; width: 851px; height: 375px;
    background: radial-gradient(ellipse 320px 180px at 425px 20px, #2a5fae 0%, #173f8a 35%, transparent 75%),
                linear-gradient(180deg, #0b1f5a 0%, #0a1a4c 60%, var(--navy-deep) 100%); }
  .hero-band { position: absolute; left: 0; bottom: 0; width: 100%; height: 7px; background: #0a1944; }
  .hero-title { position: absolute; top: 102px; width: 100%; text-align: center; color: var(--white); font-weight: 500; }
  .hero-title .line-one { display: block; font-size: 31px; line-height: 34px; }
  .hero-title .line-two { display: block; font-size: 25px; line-height: 28px; }
  .hero-lead { position: absolute; top: 173px; width: 100%; text-align: center; color: var(--white); font-size: 10.4px; line-height: 12.5px; }
  .btn-outline { position: absolute; left: 380px; top: 213px; width: 94px; height: 29px; border: 1.5px solid var(--white); border-radius: 3px;
    color: var(--white); font-size: 12px; font-weight: 600; display: flex; align-items: center; justify-content: center; }
  .carousel-dots { position: absolute; top: 351px; left: 400px; display: flex; gap: 3px; }
  .carousel-dots span { width: 11px; height: 11px; border-radius: 50%; background: #a9adb8; }
  .carousel-dots span.active { background: var(--white); }

  /* Intro */
  .intro-title { position: absolute; top: 481px; width: 100%; text-align: center; font-size: 19px; font-weight: 500; color: #1d1f22; }
  .intro-text { position: absolute; top: 509px; width: 100%; text-align: center; font-size: 9.8px; line-height: 16px; color: var(--ink-soft); }

  .services { position: absolute; top: 570px; left: 0; width: 851px; height: 160px; }
  .services::after { content: ""; position: absolute; left: 50px; right: 54px; bottom: 0; height: 40px;
    background: radial-gradient(ellipse 50% 100% at 50% 100%, rgba(0,0,0,0.07), transparent 80%); }
  .service { position: absolute; top: 0; width: 180px; margin-left: -90px; text-align: center; }
  .service svg { display: block; margin: 0 auto; height: 40px; }
  .service h3 { margin-top: 17px; font-size: 13.5px; font-weight: 500; color: var(--brand-green); }
  .service p { margin-top: 6px; font-family: "Open Sans", sans-serif; font-size: 7.4px; line-height: 12px; color: var(--muted); }

  /* Cards */
  .card { position: absolute; top: 758px; width: 175px; }
  .card-media { width: 175px; height: 80px; }
  .card h3 { margin: 10px 0 0 4px; font-size: 13px; font-weight: 500; color: #2b2f33; }
  .card p { margin: 5px 0 0 4px; font-family: "Open Sans", sans-serif; font-size: 6.9px; line-height: 12px; color: var(--muted); }

  /* Contact */
  .contact { position: absolute; left: 0; top: 932px; width: 851px; height: 192px;
    background: radial-gradient(ellipse 300px 120px at 130px 150px, rgba(140,210,245,0.55), transparent 70%),
                radial-gradient(ellipse 260px 110px at 700px 60px, rgba(140,210,245,0.45), transparent 70%),
                linear-gradient(180deg, #62bbea, var(--sky)); }
  .contact h2 { position: absolute; top: 26px; width: 100%; text-align: center; font-size: 18px; font-weight: 500; color: #153a55; }
  .field { position: absolute; background: var(--field); font-family: "Open Sans", sans-serif; font-size: 7.4px; color: var(--field-text); padding: 7px 8px; }
  .btn-submit { position: absolute; left: 389px; top: 149px; width: 85px; height: 25px; border: 1.5px solid #123048; border-radius: 2px;
    display: flex; align-items: center; justify-content: center; font-size: 11px; color: #123048; font-weight: 500; }

  /* Footer */
  .site-footer { position: absolute; left: 0; top: 1124px; width: 851px; height: 76px; background: var(--footer); color: var(--white); }
  .footer-nav { position: absolute; left: 146px; top: 22px; font-size: 9.5px; }
  .footer-nav .sep { margin: 0 6px; }
  .legal { position: absolute; left: 146px; top: 42px; font-family: "Open Sans", sans-serif; font-size: 7.4px; }
  .social { position: absolute; left: 644px; top: 23px; display: flex; gap: 8px; }
  .social span { width: 13px; height: 13px; border-radius: 50%; background: var(--white); }
</style>
</head>
<body>

<header class="site-header">
  <div class="brand"><span class="brand-dot"></span><span class="brand-name">quenvo</span></div>
  <nav class="main-nav">
    <a style="left:0">About Us</a>
    <a style="left:69px">Features</a>
    <a style="left:136px">Services</a>
    <a style="left:201px">Blog</a>
    <a style="left:248px">Support</a>
    <a style="left:312px">Resources</a>
  </nav>
</header>

<section class="hero" role="img" aria-label="Dark blue network of connected data points">
  <h1 class="hero-title"><span class="line-one">Quenvo Maps Markets to Drive</span><span class="line-two">Sales and Marketing</span></h1>
  <p class="hero-lead">Phasellus pellentesque aliquam enim Proin dui lectus cursus eu mattis laoreet viverra sit amet quam<br>Curabitur vel dolor ultrices ipsum dictum tristique Praesent vitae lacus</p>
  <div class="btn-outline">Download</div>
  <div class="carousel-dots"><span class="active"></span><span></span><span></span><span></span></div>
  <div class="hero-band"></div>
</section>

<h2 class="intro-title">Suspendisse risus ultricies volutpat condimentum</h2>
<p class="intro-text">Nunc tempus felis vitae urna Vivamus porttitor neque at volutpat rutrum purus nisi eleifend libero a tempus libero<br>lectus feugiat felis Morbi diam mauris viverra in gravida eu mattis in ante Morbi ege</p>

<section class="services">
  <div class="service" style="left:231px">
    <svg viewBox="0 0 40 40" width="40" aria-hidden="true"><path d="M28 4a8 8 0 0 0-7.5 10.6L5 30a3.2 3.2 0 0 0 4.5 4.5L25 19.1A8 8 0 0 0 35.6 11l-5 3.5-4.4-1-1-4.4z" fill="#6cbb3c"/></svg>
    <h3>Featured Service</h3>
    <p>Integer congue augue et malesuada iaculis ipsum<br>dui aliquet felis at cursus magna nisl nec elit<br>Praesent elementum elit at tellus nec</p>
  </div>
  <div class="service" style="left:425px">
    <svg viewBox="0 0 40 40" width="40" aria-hidden="true"><path d="M3 4v32h35v-2H5V4z" fill="#6cbb3c"/><path d="M7 32V20l7-9 6 7 5-6 5 8 5-3v15z" fill="#6cbb3c"/></svg>
    <h3>Data Analytics</h3>
    <p>Integer congue augue et malesuada iaculis ipsum<br>dui aliquet felis at cursus magna nisl nec elit<br>Praesent elementum elit at tellus nec</p>
  </div>
  <div class="service" style="left:619px">
    <svg viewBox="0 0 40 40" width="40" aria-hidden="true"><path d="M20 3a11 11 0 0 0-6.5 19.9c1 .8 1.5 2 1.5 3.2V28h10v-1.9c0-1.2.5-2.4 1.5-3.2A11 11 0 0 0 20 3z" fill="none" stroke="#6cbb3c" stroke-width="3"/><rect x="15" y="30" width="10" height="3" fill="#6cbb3c"/><rect x="16.5" y="34.5" width="7" height="3" rx="1.5" fill="#6cbb3c"/></svg>
    <h3>Featured Service</h3>
    <p>Integer congue augue et malesuada iaculis ipsum<br>dui aliquet felis at cursus magna nisl nec elit<br>Praesent elementum elit at tellus nec</p>
  </div>
</section>

<article class="card" style="left:147px">
  <div class="card-media" role="img" aria-label="Person working at a touch screen" style="background:linear-gradient(90deg,#9fb3c4,#dfe4e8 60%,#f2f2f2)"></div>
  <h3>What We Do</h3>
  <p>nim In massa libero interdum nec interdum vel blandit<br>sed nulla In ullamcorper est eget tempor</p>
</article>
<article class="card" style="left:341px">
  <div class="card-media" role="img" aria-label="Bubble network map of market data" style="background:linear-gradient(135deg,#eef2ee,#d6ead8 50%,#e8e2ee)"></div>
  <h3>How it Works</h3>
  <p>nim In massa libero interdum nec interdum vel blandit<br>sed nulla In ullamcorper est eget tempor</p>
</article>
<article class="card" style="left:535px">
  <div class="card-media" role="img" aria-label="Business analyst with growth charts" style="background:linear-gradient(90deg,#1a1a1a,#4a4d50 60%,#2a2a2a)"></div>
  <h3>Why Chose Us</h3>
  <p>nim In massa libero interdum nec interdum vel blandit<br>sed nulla In ullamcorper est eget tempor</p>
</article>

<section class="contact">
  <h2>Get Started Now</h2>
  <div class="field" style="left:211px;top:62px;width:138px;height:22px">Name</div>
  <div class="field" style="left:358px;top:62px;width:138px;height:22px">Email address</div>
  <div class="field" style="left:505px;top:62px;width:138px;height:22px">Phone no.</div>
  <div class="field" style="left:211px;top:91px;width:432px;height:52px">Message</div>
  <div class="btn-submit">SUBMIT</div>
</section>

<footer class="site-footer">
  <nav class="footer-nav">About Us<span class="sep">|</span>Features<span class="sep">|</span>Services<span class="sep">|</span>Blog<span class="sep">|</span>Support<span class="sep">|</span>Resources</nav>
  <p class="legal">© 2015 Company Name &nbsp;All right reserved &nbsp;Term of Use</p>
  <div class="social" aria-label="Social links"><span></span><span></span><span></span></div>
</footer>

</body>
</html>
```